Banner ads for LP that work with same theme as below banners

Love the banner ads below. Need more with attached photos. But use the same wording, font as in below banner ads. Should be LP size 1200/627 so I can use for Pixorly and LP. Looking for great ads to use as LP ads. We do lots of ads so it will be worth your time to enter this contest you will be rewarded with a ton of work. Need several banner ads that work together. So maybe 1 of the dresses, 1 of the sweater, 1 of the leggings, 1 of the jacket

Target Market(s)

Women 24-45

Industry/Entity Type

Fashion

Requirements
Must have
• Banner ads that work for LP and Pixorly
Nice to have
• Several options to choose from
Should not have
• not sure

```html
<!DOCTYPE html>
<html lang="en">
<head>
<meta charset="UTF-8">
<title>LP — Our Best Dresses Ever</title>
<link href="https://fonts.googleapis.com/css2?family=Dancing+Script:wght@500&family=Libre+Baskerville:wght@700&family=Playfair+Display:wght@700&display=swap" rel="stylesheet">
<style>
  :root {
    --page: #ffffff;
    --mist: #e9e7ee;
    --stone: #c8c5c0;
    --panel: #cdcac5;
    --bronze: #7d5326;
    --bronze-soft: #8a5e2c;
    --ink: #111111;
    --slate: #4f4f4f;
    --frame: #d9d9d9;
    --cream: #f4efe6;
  }
  * { margin: 0; padding: 0; box-sizing: border-box; }
  html, body { width: 1200px; height: 627px; overflow: hidden; background: var(--page); }
  .banner { position: relative; width: 1200px; height: 627px; overflow: hidden; background: var(--page); }

  .mist-corner { position: absolute; right: 0; top: 0; width: 620px; height: 627px; background: linear-gradient(180deg, var(--mist) 0%, #f3f2f6 100%); }
  .stone-band { position: absolute; left: 0; top: 75px; width: 1200px; height: 430px; background: var(--stone); }
  .stone-band.right { top: 25px; height: 480px; left: 1030px; width: 170px; }
  .mist-base { position: absolute; left: 0; top: 505px; width: 1200px; height: 122px; background: linear-gradient(90deg, #ffffff 0%, #ffffff 60%, var(--mist) 100%); }

  .shapes { position: absolute; inset: 0; }

  .panel {
    position: absolute; left: 203px; top: 33px; width: 827px; height: 600px;
    background: var(--panel);
    box-shadow: 0 0 40px rgba(60, 50, 70, 0.45);
  }

  .headline { position: absolute; left: 600px; top: 40px; width: 450px; text-align: center; color: var(--ink); }
  .headline .script { display: block; font-family: "Dancing Script", cursive; font-weight: 500; font-size: 66px; line-height: 1; }
  .headline .script.top { margin-left: -40px; }
  .headline .category {
    display: block; font-family: "Libre Baskerville", serif; font-weight: 700;
    font-size: 54px; letter-spacing: 0.36em; color: var(--slate); margin: 20px 0 12px 24px; line-height: 1;
  }
  .headline .script.bottom { font-size: 74px; margin-left: -90px; }

  .look { position: absolute; background: #ffffff; border: 9px solid var(--frame); box-shadow: 4px 6px 10px rgba(0,0,0,0.3); }
  .look .photo { width: 100%; height: 100%; }
  .look.sweater { left: 190px; top: 290px; width: 285px; height: 270px; transform: rotate(-9deg); }
  .look.sweater .photo { background: linear-gradient(180deg, #f3f1ef 0%, #c98f75 45%, #b45a45 100%); }
  .look.lace { left: 462px; top: 290px; width: 275px; height: 270px; transform: rotate(-9deg); }
  .look.lace .photo { background: linear-gradient(180deg, #f7f5f2 0%, #c7a27a 30%, #1b1b1b 60%, #2a2a2a 100%); }
  .look.embroidered { left: 730px; top: 292px; width: 285px; height: 265px; transform: rotate(-9deg); }
  .look.embroidered .photo { background: linear-gradient(180deg, #f7f6f5 0%, #7a5648 35%, #1a1a24 70%, #23202c 100%); }

  .cta {
    position: absolute; left: 908px; top: 584px; width: 260px;
    font-family: "Playfair Display", serif; font-weight: 700; font-size: 25px;
    color: var(--cream); letter-spacing: 0.02em; white-space: nowrap;
  }
</style>
</head>
<body>
<main class="banner">
  <div class="mist-corner"></div>
  <div class="stone-band"></div>
  <div class="stone-band right"></div>
  <div class="mist-base"></div>

  <svg class="shapes" width="1200" height="627" viewBox="0 0 1200 627" aria-hidden="true">
    <polygon points="0,0 630,0 560,75 0,75" fill="var(--bronze)"/>
  </svg>

  <div class="panel"></div>

  <svg class="shapes" width="1200" height="627" viewBox="0 0 1200 627" aria-hidden="true">
    <polygon points="203,33 594,33 560,75 203,75" fill="var(--bronze-soft)"/>
    <polygon points="800,627 862,575 1200,575 1200,627" fill="var(--bronze)"/>
  </svg>

  <h1 class="headline">
    <span class="script top">Our Best</span>
    <span class="category">DRESSES</span>
    <span class="script bottom">Ever!</span>
  </h1>

  <figure class="look sweater"><div class="photo" role="img" aria-label="Model in a rust lace-up knit sweater dress"></div></figure>
  <figure class="look lace"><div class="photo" role="img" aria-label="Model in a black lace sleeveless dress"></div></figure>
  <figure class="look embroidered"><div class="photo" role="img" aria-label="Model in a black dress with red floral embroidery"></div></figure>

  <div class="cta">SHOP THE LOOK</div>
</main>
</body>
</html>
```